Coastal Learner Bureau business cards

Australian company about to start offering its services. We recruit international students to come to study English, vocational education and postgraduate courses in Australia. We help them find the institution and select the right city they want to come to Australia. We are a young, online oriented and supportive agency. Our clients are between 18 and 35 years old, mainly University students, young professionals or people with work experience. We provide much more information that any other agency offer. We administrate a Facebook group with more than 11.000 members that daily ask questions about general information when coming to Australia, while they are here and even after they leave the country

Target Market(s)

International students from South America, Central America and Europe

Industry/Entity Type

Student

Contact Information for Business Card

Tomas Bilbrea
Managing Director
tomas@kelvarin.com.au
www.kelvoria.com.au
+61 491058264
Melbourne, Australia

Font styles to use
Serif
Sans Serif

Colors

Designer to choose colors to be used in the design.

Requirements
Must have
• Horizontal design
• Standard business card size and shape. If font uses green or yellow colours, they will have to match the ones from the logo
Nice to have
• UPDATE: Use the contents of the green image to design one of the card sides. Use our logo in the background of that side as watermark.
• Passport image, or immigration stamps. A picture of the Yarra River (from Melbourne) would be cool as well.
Should not have
• Non-standard business card size and shape
• Not black as the background colour of any sides as we are not a VIP agency or a hight class service. We are orientes to young people and they like colours, pictures, something attractive.
• Vertical design
• NO YELLOW or BLACK AS THE BACKGROUND COLOUR OF ANY SIDE OF THE BIZ CARD

```html
<!DOCTYPE html>
<html lang="en">
<head>
<meta charset="utf-8">
<title>Coastal Learner Bureau – Business Cards</title>
<link rel="stylesheet" href="https://fonts.googleapis.com/css2?family=Arimo:wght@400;700&display=swap">
<style>
  :root {
    --page-bg: #e9e9e9;
    --brand-green: #1d6b3c;
    --brand-yellow: #f0c419;
    --ink: #1f1f1f;
    --paper: #f7f1f1;
    --sky-top: #5f9fd6;
    --sky-low: #b9d6ee;
    --park-green: #5b7f3a;
    --water: #6f8f96;
    --stamp-tint: #d9c9cf;
    --stamp-teal: #8cc4b8;
  }
  * { box-sizing: border-box; margin: 0; padding: 0; }
  html, body {
    width: 1200px; height: 997px; overflow: hidden;
    background: var(--page-bg);
    font-family: "Arimo", Arial, sans-serif;
    color: var(--ink);
  }
  .canvas { position: relative; width: 1200px; height: 997px; }
  .card {
    position: absolute; width: 720px; height: 411px;
    border-radius: 22px; overflow: hidden;
    box-shadow: 0 10px 28px rgba(0,0,0,0.25);
  }

  /* Front side */
  .card-front { left: 120px; top: 60px; }
  .front-photo {
    position: absolute; inset: 0;
    background: linear-gradient(180deg, var(--sky-top) 0%, var(--sky-low) 52%, var(--park-green) 66%, var(--water) 80%, var(--park-green) 100%);
  }
  .front-brand {
    position: absolute; left: 200px; top: 78px;
    display: flex; align-items: center; gap: 14px;
    font-size: 64px; font-weight: 700; color: var(--brand-green);
  }
  .brand-dot { width: 22px; height: 22px; border-radius: 50%; background: var(--brand-yellow); }
  .web-band {
    position: absolute; right: 0; top: 138px;
    width: 330px; height: 46px;
    background: var(--brand-green);
    display: flex; align-items: center; justify-content: center;
    color: var(--brand-yellow); font-weight: 700; font-size: 22px;
  }
  .front-stamp {
    position: absolute; left: 20px; bottom: 20px;
    width: 330px; height: 150px; border-radius: 14px;
    background: linear-gradient(135deg, rgba(240,196,25,0.85), rgba(240,196,25,0.55));
  }

  /* Back side */
  .card-back { left: 360px; top: 520px; background: var(--paper); }
  .back-stamps {
    position: absolute; inset: 0;
    background:
      radial-gradient(circle at 85% 18%, rgba(140,196,184,0.6) 0, rgba(140,196,184,0) 26%),
      radial-gradient(circle at 20% 25%, var(--stamp-tint) 0, rgba(217,201,207,0) 30%),
      radial-gradient(circle at 25% 85%, var(--stamp-tint) 0, rgba(217,201,207,0) 28%),
      radial-gradient(circle at 78% 55%, rgba(190,200,225,0.7) 0, rgba(190,200,225,0) 28%),
      var(--paper);
  }
  .back-brand {
    position: absolute; left: 250px; top: 92px;
    display: flex; align-items: center; gap: 12px;
    font-size: 56px; font-weight: 700; color: var(--brand-green);
  }
  .divider {
    position: absolute; left: 30px; right: 30px; top: 236px;
    height: 2px; background: var(--brand-green);
  }
  .person { position: absolute; left: 36px; top: 204px; }
  .person-name { font-size: 22px; font-weight: 700; color: var(--brand-green); letter-spacing: 0.5px; }
  .person-title { margin-top: 14px; font-size: 18px; }
  .company {
    position: absolute; right: 36px; top: 248px;
    text-align: right; font-size: 17px; line-height: 1.3;
  }
  .company-name { font-weight: 700; color: var(--brand-green); font-size: 17px; }
  .contacts { position: absolute; left: 36px; bottom: 34px; list-style: none; }
  .contacts li { display: flex; align-items: center; gap: 12px; font-size: 20px; margin-top: 8px; }
  .contact-icon { width: 22px; height: 22px; flex: none; }
</style>
</head>
<body>
<main class="canvas">

  <section class="card card-front" aria-label="Card front">
    <div class="front-photo" role="img" aria-label="Photo of the Yarra River in Melbourne with the city skyline, blue sky and green parkland"></div>
    <div class="front-brand"><span class="brand-dot"></span><span>Kelvoria</span></div>
    <div class="web-band">www.kelvoria.com.au</div>
    <div class="front-stamp" role="img" aria-label="Large yellow immigration approval stamp"></div>
  </section>

  <section class="card card-back" aria-label="Card back">
    <div class="back-stamps" role="img" aria-label="Passport page background with faint immigration stamps"></div>
    <div class="back-brand"><span class="brand-dot"></span><span>Kelvoria</span></div>
    <div class="divider"></div>

    <div class="person">
      <p class="person-name">TOMAS BILBREA</p>
      <p class="person-title">Managing Director</p>
    </div>

    <div class="company">
      <p class="company-name">KELVORIA PVT LTD.</p>
      <p>228 Marlow Lane, 9th Street Box 412,</p>
      <p>Melbourne, Australia 30561</p>
    </div>

    <ul class="contacts">
      <li>
        <svg class="contact-icon" viewBox="0 0 22 22" aria-hidden="true">
          <circle cx="11" cy="11" r="11" fill="var(--brand-green)"/>
          <path d="M7 6.5c.6-.6 1.4-.5 1.8.1l1 1.5c.3.5.2 1.1-.2 1.5l-.6.5c.5 1.1 1.4 2 2.5 2.5l.5-.6c.4-.4 1-.5 1.5-.2l1.5 1c.6.4.7 1.2.1 1.8l-.7.7c-2.8.9-7.8-4.1-6.9-6.9z" fill="#fff"/>
        </svg>
        <span>+61 491058264</span>
      </li>
      <li>
        <svg class="contact-icon" viewBox="0 0 22 22" aria-hidden="true">
          <circle cx="11" cy="11" r="11" fill="var(--brand-green)"/>
          <rect x="5.5" y="7" width="11" height="8" rx="1" fill="#fff"/>
          <path d="M5.8 7.4 11 11.4l5.2-4" fill="none" stroke="var(--brand-green)" stroke-width="1.2"/>
        </svg>
        <span>tomas@kelvarin.com.au</span>
      </li>
    </ul>
  </section>

</main>
</body>
</html>
```